Step and Repeat Backdrop for wedding reception photo booth

Would like to have a Step and Repeat Backdrop (8 foot high by 10 foot wide) that incorporates the wedding logo (attached) and the names Helen and Gavin. Background should be white, and wedding colors are burgundy and gold. Show me creativity :-) I have included some random samples.

```html
<!DOCTYPE html>
<html lang="en">
<head>
<meta charset="utf-8">
<title>Helen &amp; Gavin – Step and Repeat Backdrop</title>
<link rel="stylesheet" href="https://fonts.googleapis.com/css2?family=Cinzel:wght@500&family=Dancing+Script:wght@700&display=swap">
<style>
  :root {
    --stage-grey: #808080;
    --backdrop-white: #ffffff;
    --gold-light: #c9a86a;
    --gold-deep: #94703a;
    --ring-gold: #9a7a45;
  }
  html, body {
    margin: 0;
    padding: 0;
    width: 766px;
    height: 1200px;
    overflow: hidden;
    background: var(--stage-grey);
  }
  .backdrop {
    position: absolute;
    left: 33px;
    top: 320px;
    width: 700px;
    height: 560px;
    background: var(--backdrop-white);
    overflow: hidden;
  }
  .repeat-pattern {
    position: absolute;
    inset: 0;
    width: 700px;
    height: 560px;
  }
  .repeat-pattern .monogram-name {
    font-family: "Cinzel", serif;
    font-weight: 500;
    font-size: 15px;
    fill: var(--gold-light);
    text-anchor: middle;
    dominant-baseline: central;
    letter-spacing: 0.5px;
  }
  .center-ring {
    fill: var(--backdrop-white);
  }
  .center-ring-line {
    fill: none;
    stroke: var(--ring-gold);
    stroke-width: 1;
  }
  .couple-names {
    position: absolute;
    left: 178px;
    top: 107px;
    width: 344px;
    height: 344px;
    display: flex;
    flex-direction: column;
    align-items: center;
    justify-content: center;
    font-family: "Dancing Script", cursive;
    font-weight: 700;
    color: var(--gold-deep);
    margin: 0;
  }
  .couple-names .partner {
    display: block;
    font-size: 84px;
    line-height: 0.95;
  }
  .couple-names .partner-two {
    margin-left: 14px;
  }
  .couple-names .ampersand {
    display: block;
    font-size: 46px;
    line-height: 0.9;
    margin: 2px 0;
  }
</style>
</head>
<body>
  <main class="backdrop">
    <svg class="repeat-pattern" viewBox="0 0 700 560" aria-hidden="true">
      <g class="pattern-row">
        <text class="monogram-name" x="42" y="43">H&amp;G</text><text class="monogram-name" x="125" y="43">H&amp;G</text><text class="monogram-name" x="208" y="43">H&amp;G</text><text class="monogram-name" x="291" y="43">H&amp;G</text><text class="monogram-name" x="374" y="43">H&amp;G</text><text class="monogram-name" x="457" y="43">H&amp;G</text><text class="monogram-name" x="540" y="43">H&amp;G</text><text class="monogram-name" x="623" y="43">H&amp;G</text>
      </g>
      <g class="pattern-row">
        <text class="monogram-name" x="77" y="95">H&amp;G</text><text class="monogram-name" x="160" y="95">H&amp;G</text><text class="monogram-name" x="243" y="95">H&amp;G</text><text class="monogram-name" x="326" y="95">H&amp;G</text><text class="monogram-name" x="409" y="95">H&amp;G</text><text class="monogram-name" x="492" y="95">H&amp;G</text><text class="monogram-name" x="575" y="95">H&amp;G</text><text class="monogram-name" x="658" y="95">H&amp;G</text>
      </g>
      <g class="pattern-row">
        <text class="monogram-name" x="42" y="147">H&amp;G</text><text class="monogram-name" x="125" y="147">H&amp;G</text><text class="monogram-name" x="208" y="147">H&amp;G</text><text class="monogram-name" x="291" y="147">H&amp;G</text><text class="monogram-name" x="374" y="147">H&amp;G</text><text class="monogram-name" x="457" y="147">H&amp;G</text><text class="monogram-name" x="540" y="147">H&amp;G</text><text class="monogram-name" x="623" y="147">H&amp;G</text>
      </g>
      <g class="pattern-row">
        <text class="monogram-name" x="77" y="200">H&amp;G</text><text class="monogram-name" x="160" y="200">H&amp;G</text><text class="monogram-name" x="243" y="200">H&amp;G</text><text class="monogram-name" x="326" y="200">H&amp;G</text><text class="monogram-name" x="409" y="200">H&amp;G</text><text class="monogram-name" x="492" y="200">H&amp;G</text><text class="monogram-name" x="575" y="200">H&amp;G</text><text class="monogram-name" x="658" y="200">H&amp;G</text>
      </g>
      <g class="pattern-row">
        <text class="monogram-name" x="42" y="252">H&amp;G</text><text class="monogram-name" x="125" y="252">H&amp;G</text><text class="monogram-name" x="208" y="252">H&amp;G</text><text class="monogram-name" x="291" y="252">H&amp;G</text><text class="monogram-name" x="374" y="252">H&amp;G</text><text class="monogram-name" x="457" y="252">H&amp;G</text><text class="monogram-name" x="540" y="252">H&amp;G</text><text class="monogram-name" x="623" y="252">H&amp;G</text>
      </g>
      <g class="pattern-row">
        <text class="monogram-name" x="77" y="304">H&amp;G</text><text class="monogram-name" x="160" y="304">H&amp;G</text><text class="monogram-name" x="243" y="304">H&amp;G</text><text class="monogram-name" x="326" y="304">H&amp;G</text><text class="monogram-name" x="409" y="304">H&amp;G</text><text class="monogram-name" x="492" y="304">H&amp;G</text><text class="monogram-name" x="575" y="304">H&amp;G</text><text class="monogram-name" x="658" y="304">H&amp;G</text>
      </g>
      <g class="pattern-row">
        <text class="monogram-name" x="42" y="356">H&amp;G</text><text class="monogram-name" x="125" y="356">H&amp;G</text><text class="monogram-name" x="208" y="356">H&amp;G</text><text class="monogram-name" x="291" y="356">H&amp;G</text><text class="monogram-name" x="374" y="356">H&amp;G</text><text class="monogram-name" x="457" y="356">H&amp;G</text><text class="monogram-name" x="540" y="356">H&amp;G</text><text class="monogram-name" x="623" y="356">H&amp;G</text>
      </g>
      <g class="pattern-row">
        <text class="monogram-name" x="77" y="408">H&amp;G</text><text class="monogram-name" x="160" y="408">H&amp;G</text><text class="monogram-name" x="243" y="408">H&amp;G</text><text class="monogram-name" x="326" y="408">H&amp;G</text><text class="monogram-name" x="409" y="408">H&amp;G</text><text class="monogram-name" x="492" y="408">H&amp;G</text><text class="monogram-name" x="575" y="408">H&amp;G</text><text class="monogram-name" x="658" y="408">H&amp;G</text>
      </g>
      <g class="pattern-row">
        <text class="monogram-name" x="42" y="461">H&amp;G</text><text class="monogram-name" x="125" y="461">H&amp;G</text><text class="monogram-name" x="208" y="461">H&amp;G</text><text class="monogram-name" x="291" y="461">H&amp;G</text><text class="monogram-name" x="374" y="461">H&amp;G</text><text class="monogram-name" x="457" y="461">H&amp;G</text><text class="monogram-name" x="540" y="461">H&amp;G</text><text class="monogram-name" x="623" y="461">H&amp;G</text>
      </g>
      <g class="pattern-row">
        <text class="monogram-name" x="77" y="513">H&amp;G</text><text class="monogram-name" x="160" y="513">H&amp;G</text><text class="monogram-name" x="243" y="513">H&amp;G</text><text class="monogram-name" x="326" y="513">H&amp;G</text><text class="monogram-name" x="409" y="513">H&amp;G</text><text class="monogram-name" x="492" y="513">H&amp;G</text><text class="monogram-name" x="575" y="513">H&amp;G</text><text class="monogram-name" x="658" y="513">H&amp;G</text>
      </g>

      <circle class="center-ring" cx="350" cy="279" r="174"/>
      <circle class="center-ring-line" cx="353" cy="274" r="172"/>
      <ellipse class="center-ring-line" cx="348" cy="284" rx="171" ry="173"/>
    </svg>

    <h1 class="couple-names">
      <span class="partner partner-one">Helen</span>
      <span class="ampersand">&amp;</span>
      <span class="partner partner-two">Gavin</span>
    </h1>
  </main>
</body>
</html>
```